Marlow Estate Fixers (Handyman / Home Improvement Company)

Looking for a double sided professional looking business card with Logo attached to be highlighted on one side and throwing in an image of a handyman as an option would be nice to see as well. We are a company focused on providing quality Handyman and Home improvement services in a timely manner that is done right the first time with integrity

Industry/Entity Type

Handyman / Home Improvement

Contact Information for Business Card

(LOGO, Name, Mobile and office phone numbers, email) on front side of card, (the words "The SOLUTION to all of your Handyman and Home Improvement needs" followed by "Family Owned and Operated" at the very bottom) on the back.

Colors
EB3D1F
EC4F4E
F09395
F8D3D4
FCEDEE

Requirements
Must have
• Red, Gray, Black Color scheme
Should not have
• No Yellow or Blue colors

```html
<!DOCTYPE html>
<html lang="en">
<head>
<meta charset="UTF-8">
<title>Marlow Estate Fixers – Business Card</title>
<link href="https://fonts.googleapis.com/css2?family=Montserrat:wght@400;600;700;800&family=Oswald:wght@700&display=swap" rel="stylesheet">
<style>
  :root {
    --red: #eb2e2f;
    --red-deep: #c81f22;
    --charcoal: #3a3a3a;
    --ink: #1e1e1e;
    --white: #ffffff;
    --stage: #1c1c1c;
    --overall-blue-free: #6a6a6a;
  }
  * { margin: 0; padding: 0; box-sizing: border-box; }
  html, body { width: 1200px; height: 1059px; overflow: hidden; }
  body {
    background: var(--stage);
    font-family: "Montserrat", sans-serif;
    position: relative;
  }
  .card {
    position: absolute;
    left: 262px;
    width: 715px;
    height: 410px;
    border-radius: 24px;
    overflow: hidden;
  }
  /* Front */
  .card--front { top: 94px; background: var(--white); }
  .front-brand {
    position: absolute;
    left: 420px; top: 70px;
    width: 265px;
    display: flex; align-items: center; gap: 12px;
  }
  .front-brand .mark {
    width: 22px; height: 22px; flex: none;
    background: var(--red);
  }
  .brand-name {
    font-weight: 800;
    font-size: 30px;
    line-height: 1.05;
    text-transform: uppercase;
    letter-spacing: 0.5px;
  }
  .front-brand .brand-name { color: var(--red); }
  .holder-name {
    position: absolute; left: 35px; top: 250px;
    font-weight: 700; font-size: 29px; color: var(--red);
  }
  .holder-role {
    position: absolute; left: 35px; top: 291px;
    font-size: 19px; color: var(--ink);
  }
  .divider {
    position: absolute; left: 35px; top: 330px;
    width: 648px; height: 2px; background: var(--charcoal);
  }
  .contacts {
    position: absolute; left: 38px; top: 343px;
    display: flex; align-items: center; gap: 20px;
    font-size: 18.5px; color: var(--ink);
  }
  .contact { display: flex; align-items: center; gap: 10px; white-space: nowrap; }
  .contact svg { flex: none; fill: var(--red); }
  .edge-band { position: absolute; left: 0; bottom: 0; width: 100%; height: 13px; }

  /* Back */
  .card--back { top: 529px; background: var(--red); color: var(--white); }
  .handyman-art {
    position: absolute; left: 32px; top: 24px;
    width: 194px; height: 373px;
    border-radius: 90px 90px 30px 30px;
    background: linear-gradient(180deg, #f0b98c 0%, #8c8c8c 45%, #5c5c5c 80%, #7b4a2a 100%);
    opacity: 0.9;
  }
  .tagline {
    position: absolute; left: 250px; width: 410px;
    text-align: center;
  }
  .tagline__lead {
    top: 14px; font-weight: 700; font-size: 22px;
  }
  .tagline__main {
    font-family: "Oswald", sans-serif; font-weight: 700;
    font-size: 34px; line-height: 1; transform: scaleY(1.1);
  }
  .tagline__main--one { top: 51px; }
  .tagline__main--two { top: 96px; }
  .back-brand {
    position: absolute; left: 317px; top: 195px; width: 275px;
    display: flex; align-items: center; justify-content: center; gap: 14px;
  }
  .back-brand .mark {
    width: 26px; height: 26px; flex: none;
    border-radius: 50%; background: var(--white);
  }
  .back-brand .brand-name { color: var(--white); font-size: 34px; }
  .footer-line {
    position: absolute; left: 250px; width: 410px; top: 363px;
    text-align: center; font-weight: 700; font-size: 23.5px;
  }
</style>
</head>
<body>

<section class="card card--front" aria-label="Business card front">
  <div class="front-brand">
    <span class="mark"></span>
    <div class="brand-name">Marlow<br>Estate<br>Fixers</div>
  </div>

  <div class="holder-name">Daniel Reeve</div>
  <div class="holder-role">Owner</div>
  <div class="divider"></div>

  <div class="contacts">
    <div class="contact">
      <svg width="13" height="22" viewBox="0 0 13 22" aria-hidden="true"><path d="M2 0h9a2 2 0 0 1 2 2v18a2 2 0 0 1-2 2H2a2 2 0 0 1-2-2V2a2 2 0 0 1 2-2zm0 3v14h9V3zm4.5 15.5a1 1 0 1 0 0 2 1 1 0 0 0 0-2z"/></svg>
      <span>055-284 613 970</span>
    </div>
    <div class="contact">
      <svg width="20" height="16" viewBox="0 0 20 16" aria-hidden="true"><path d="M1 5C3 1 17 1 19 5l-1 2-4-1V4H6v2L2 7zM5 8h10l3 8H2zm3 2v2h4v-2z"/></svg>
      <span>055-284 613 971</span>
    </div>
    <div class="contact">
      <svg width="20" height="15" viewBox="0 0 20 15" aria-hidden="true"><path d="M0 0h20v15H0zm2 2v1l8 6 8-6V2l-8 5z"/></svg>
      <span>hello@marlowfixers.com</span>
    </div>
  </div>

  <svg class="edge-band" viewBox="0 0 715 13" preserveAspectRatio="none" aria-hidden="true">
    <rect x="0" y="0" width="358" height="13" fill="var(--red)"/>
    <polygon points="354,0 366,13 715,13 715,0" fill="var(--charcoal)"/>
    <polygon points="356,0 362,0 369,13 363,13" fill="var(--white)"/>
  </svg>
</section>

<section class="card card--back" aria-label="Business card back">
  <div class="handyman-art" role="img" aria-label="Illustration of a smiling handyman in overalls giving a thumbs up and holding a toolbox"></div>

  <div class="tagline tagline__lead">Your SOLUTION to all of</div>
  <div class="tagline tagline__main tagline__main--one">your Handyman and</div>
  <div class="tagline tagline__main tagline__main--two">Home Improvement Needs</div>

  <div class="back-brand">
    <span class="mark"></span>
    <div class="brand-name">Marlow<br>Estate<br>Fixers</div>
  </div>

  <div class="footer-line">Family Owned and Operated</div>
</section>

</body>
</html>
```